Process Serving Company needs a letterhead design

Looking to have a letterhead designed for letters to attorneys advertising our business. We would like something eye catching but professional. Colors and logos are attached. Please add "Process Service and Attorney Support" near the logo or header

Target Market(s)

Attorneys

Font styles to use
Serif
Sans Serif

Colors
33a6d7
0255a3
85cae6
cee9f5
ecf7fb

```html
<!DOCTYPE html>
<html lang="en">
<head>
<meta charset="utf-8">
<title>Canyon Swift Serve Letterhead</title>
<link href="https://fonts.googleapis.com/css2?family=Arimo:wght@700&family=Source+Sans+3:wght@400;600&display=swap" rel="stylesheet">
<style>
  :root{
    --sky:#33a6d7;
    --navy:#0255a3;
    --light-blue:#85cae6;
    --ink:#4a4a4a;
    --ink-dark:#3a3a3a;
    --paper:#ffffff;
    --backdrop:#ececec;
  }
  *{margin:0;padding:0;box-sizing:border-box}
  html,body{width:1059px;height:1200px;overflow:hidden;background:var(--backdrop)}
  .letterhead{
    position:absolute;left:104px;top:0;width:850px;height:1200px;
    background:var(--paper);overflow:hidden;
    font-family:"Source Sans 3",sans-serif;color:var(--ink);
  }
  .brand{
    position:absolute;left:0;right:0;top:58px;
    display:flex;justify-content:center;align-items:center;gap:14px;
  }
  .brand-mark{width:26px;height:26px;background:var(--sky)}
  .brand-name{
    font-family:"Source Sans 3",sans-serif;font-weight:600;
    font-size:34px;letter-spacing:1px;color:var(--sky);text-transform:uppercase;
  }
  .greeting{
    position:absolute;left:73px;top:276px;
    font-family:"Arimo",sans-serif;font-weight:700;font-size:18px;color:var(--ink-dark);
  }
  .body-copy{position:absolute;left:73px;top:327px;width:713px}
  .body-copy p{
    font-size:16.5px;line-height:22.2px;text-align:justify;margin-bottom:22px;
  }
  .signature{
    position:absolute;left:72px;top:848px;width:160px;height:76px;
    background:linear-gradient(90deg,#e4e4e4,#f4f4f4);
  }
  .footer-address{
    position:absolute;left:0;right:0;top:1130px;text-align:center;
    font-size:12px;color:var(--ink-dark);
  }
  .footer-contacts{
    position:absolute;left:0;right:0;top:1150px;
    display:flex;justify-content:center;gap:8px;
    font-size:12px;color:var(--ink-dark);
  }
  .footer-contacts span{display:flex;align-items:center;gap:3px}
  .footer-contacts svg{width:10px;height:10px;fill:var(--sky)}
  .footer-band{position:absolute;left:0;bottom:0;width:850px;height:34px;background:var(--navy)}
  .footer-tab{
    position:absolute;left:31px;width:788px;top:1166px;height:16px;
    background:var(--paper);border-radius:0 0 10px 10px;
  }
  .footer-rule{
    position:absolute;left:40px;width:774px;top:1172px;height:4px;
    background:var(--light-blue);border-radius:2px;
  }
</style>
</head>
<body>
<main class="letterhead">
  <header class="brand">
    <div class="brand-mark"></div>
    <div class="brand-name">Canyon Swift Serve</div>
  </header>

  <h1 class="greeting">Dear Mr. Hale,</h1>

  <section class="body-copy">
    <p>Lorem Ipsum is simply dummy text of the printing and typesetting industry. Lorem Ipsum has been the industry's standard dummy text ever since the 1500s, when an unknown printer took a galley of type and scrambled it to make a type specimen book. It has survived not only five centuries, but also the leap into electronic typesetting, remaining essentially unchanged.</p>
    <p>The standard chunk of Lorem Ipsum used since the 1500s is reproduced below for those interested. Sections 1.10.32 and 1.10.33 from "de Finibus Bonorum et Malorum" by Quintus are also reproduced in their exact original form, accompanied by English versions from the 1914 translation by H. Ashford</p>
    <p>Lorem Ipsum is simply dummy text of the printing and typesetting industry. Lorem Ipsum has been the industry's standard dummy text ever since the 1500s, when an unknown printer took a galley of type and scrambled it to make a type specimen book. It has survived not only five centuries, but also the leap into electronic typesetting, remaining essentially unchanged. It was popularised in the</p>
    <p>The standard chunk of Lorem Ipsum used since the 1500s is reproduced below for those interested. Sections 1.10.32 and 1.10.33 from "de Finibus Bonorum et Malorum" by Quintus are also reproduced in their exact original form, accompanied by English versions from the 1914 translation by H. Ashford</p>
  </section>

  <div class="signature" role="img" aria-label="Handwritten signature of the sender"></div>

  <footer>
    <div class="footer-address">4120 E Mesa Ridge Rd #210 Tempe AZ 85281</div>
    <div class="footer-contacts">
      <span><svg viewBox="0 0 10 10"><path d="M2 0l2 2-1 1.5c.8 1.5 2 2.7 3.5 3.5L8 6l2 2-1.5 2C4 9.5.5 6 0 1.5z"/></svg>480-555-0142</span>
      <span><svg viewBox="0 0 10 10"><path d="M2 0h6v3h2v5H8v2H2V8H0V3h2zm1 1v2h4V1zm0 5v3h4V6z"/></svg>480-555-0142</span>
      <span><svg viewBox="0 0 10 10"><path d="M0 2h10v6H0zm1 .8v.4l4 2.6 4-2.6v-.4z"/></svg>Info@CanyonSwift.com</span>
      <span><svg viewBox="0 0 10 10"><circle cx="5" cy="5" r="5"/></svg>www.CanyonSwift.com</span>
    </div>
    <div class="footer-band"></div>
    <div class="footer-tab"></div>
    <div class="footer-rule"></div>
  </footer>
</main>
</body>
</html>
```